Presentation Brochure and Sample Box Design for Varnex Board

Varnex Board is our range of aluminium composite panel that our company supplies to the signage and shop fitting industries.
the range is divided into 3 sections: Signage Grade - Light Commercial Grade and Commercial Grade.
We require an, A4 double-sided folding brochure (swatch book) that folds 3 ways, opening once and then a second time to lay out 3 pages flat.

There should be a front and back cover.

The inside cover should be reserved with text blocks for written information about the composite panel.

The opposite page on the right when you first open the brochure should have all our Commercial Grade colours, which are the timber finishes and the 4mm black, white and metallic silver.

When the brochure is folded out a second time, showing all three inside pages flat, the two inside pages on the right (next to the inside cover with the written information) should show all our Signage Grade colours, followed by the Light Commercial Grade colours.
Each colour in each section should have the product code beneath the swatch.

This brochure should have a modern and professional feel suitable for presenting to signees, shop fitters and interiors designers.

We also require a box design to contain aluminium composite panel samples of all the colours in the range.

Please refer to the template attached for the box dimensions and layout.

The box should tie in with the brochure as a complete package with a modern and professional look suitable for presenting to shop fitters and interior designers.

Finally we require a small label sticker to be stuck on the back of each sample. On the sticker should be the Varnex Board logo, a space to put the product code for the sample colour and the phone number 1300 584 906.

To summarise, this package project includes:
1 tri-folding A4 brochure,
1 sample box package design
1 sample sticker label.

Please refer to the attachments for the Varnex Board logo in two formats - the colour swatch book and template for the sample box.
The Logo may be shown with either the original blue text or with the text in white. The blue icon colour should not change.

Target Market(s)

Signage, shop fitting and interior design

Font styles to use
Serif
Sans Serif

Requirements
Must have
• A modern, neat and professional upmarket look suitable for presenting to shop fitters and interior designers.
Nice to have
• A slick and classy look that makes you want to take home the box or brochure even if you're not interested in the product.
Should not have
• A cheap, untidy, low market look with too many colours.

```html
<!DOCTYPE html>
<html lang="en">
<head>
<meta charset="utf-8">
<title>Varnex Board – Brochure, Sample Box and Label</title>
<link href="https://fonts.googleapis.com/css2?family=Montserrat:wght@300;400;500;600;700&family=Open+Sans:wght@400;600&display=swap" rel="stylesheet">
<style>
:root{
  --navy:#2b3a63;
  --navy-deep:#2e4566;
  --blue:#2f8fd6;
  --ink:#222;
  --muted:#777;
  --board:#e3e3e3;
  --cover-grey:#3f3f3f;
  --band:#1c1c1c;
  --paper:#fff;
  --undercoat:#e2e3e5;
  --sticker-navy:#2e3445;
}
*{box-sizing:border-box;margin:0;padding:0}
html,body{width:757px;height:1200px;overflow:hidden}
body{background:linear-gradient(180deg,#e6e6e6,#d9d9d9);font-family:"Montserrat",sans-serif;color:var(--ink);position:relative}

/* ---------- shared ---------- */
.page{position:absolute;width:231px;height:319px;background:var(--paper);overflow:hidden}
.brand{display:inline-flex;align-items:center;gap:3px}
.brand-mark{display:inline-block;width:5px;height:5px;background:var(--blue)}
.brand-name{font-family:"Montserrat",sans-serif;font-weight:600;text-transform:uppercase;letter-spacing:.12em;white-space:nowrap}
.photo{position:absolute}

/* ---------- swatch sheets ---------- */
.sheet-head{display:flex;justify-content:space-between;align-items:flex-end;margin:0 26px;padding-bottom:2px;border-bottom:.5px solid var(--navy)}
.sheet-head .brand-name{font-size:6px;color:var(--navy)}
.sheet-title{font-size:4.4px;font-weight:600;color:var(--navy);text-transform:uppercase;letter-spacing:.02em}
.sheet-body{margin:0 26px}
.swatches{display:grid;grid-template-columns:repeat(3,51px);column-gap:13.5px;row-gap:7px;margin-top:9px}
.swatches.tight{row-gap:4.5px;margin-top:5px}
.sec{font-size:4.3px;font-weight:600;color:var(--navy);text-transform:uppercase;border-bottom:.5px solid var(--navy);padding-bottom:1.5px;align-self:end;line-height:1.15}
.sec.wide{grid-column:span 2}
.sec.full{grid-column:span 3}
.pair{display:flex;flex-direction:column}
.chips{display:flex;gap:2px}
.chip{width:24.5px;height:24px;border:.5px solid #c9c9c9;border-radius:1.5px;display:flex;align-items:flex-end;justify-content:center;padding-bottom:2px;text-align:center;font-size:2.5px;font-weight:600;line-height:1.05;text-transform:uppercase;color:#333}
.chip.dk{color:#fff;border-color:transparent}
.code{font-size:2.5px;color:#666;margin-top:2.5px;height:5px;font-family:"Open Sans",sans-serif}

.w{background:linear-gradient(135deg,#fff 0 30%,#e9e9e9 42%,#fff 55%,#f3f3f3)}
.mw{background:#fafafa}
.u{background:var(--undercoat)}
.k{background:#050505}
.r{background:#e3191f}
.y{background:#f5e400}
.pb{background:#0b86c9}
.rb{background:#25338a}
.fg{background:#114a30}
.hr{background:#7a1f2e}
.o{background:#ef5523}
.nb{background:#14234d}
.ch{background:#d9d7c9}
.eg{background:#0b9a48}
.ms{background:#c3c4bd}
.sg{background:#22232b}
.bs{background:linear-gradient(160deg,#bfc2c6,#8e949a 50%,#c8ccd0)}
.ra{background:linear-gradient(160deg,#c6c6c6,#a9a9a9)}
.gold{background:linear-gradient(135deg,#f2e3a6,#cdb46a 50%,#f4e7b5)}
.cu{background:linear-gradient(135deg,#c98a5a,#8f552f 55%,#b8764a)}
.bg{background:linear-gradient(135deg,#e6cf8e,#c8ad62)}
.mir{background:linear-gradient(135deg,#eee,#b6b6b6 50%,#efefef)}
.emb{background:linear-gradient(135deg,#d8d8d8,#9d9d9d 50%,#dcdcdc)}
.rust{background:linear-gradient(135deg,#a8412a,#6f2417)}
.ant{background:linear-gradient(135deg,#d3d3d3,#8e8e8e 50%,#c9c9c9)}
.ss{background:linear-gradient(135deg,#b8c0c8,#7c8791)}
.wd1{background:linear-gradient(90deg,#a35b2d,#7c3f1b,#b56a38,#8a4a22)}
.wd2{background:linear-gradient(90deg,#7a3a20,#5c2914,#8a4528)}
.wd3{background:linear-gradient(90deg,#8a5a3c,#5e3a24,#946648)}
.wd4{background:linear-gradient(90deg,#6b4430,#3f2618,#74503a)}
.wd5{background:linear-gradient(90deg,#d0a870,#b8894f,#d6b07a)}
.wd6{background:linear-gradient(90deg,#8e5a3a,#6a3f26,#a06a48)}
.pm{background:#cbc7b3}
.pk{background:#0a0a0a}

/* ---------- row 1 ---------- */
.p-sig2{left:33px;top:33px}
.p-sig2 .sheet-head{margin-top:20px}
.p-sig2 .sheet-head.second{margin-top:10px}
.p-back{left:264px;top:33px;background:var(--cover-grey)}
.p-front{left:495px;top:33px;background:var(--band)}
.cover-word{position:absolute;left:0;right:0;top:158px;text-align:center}
.cover-word .brand-name{font-size:13px;color:#8c8c8c;letter-spacing:.14em;font-weight:500}
.cover-band{position:absolute;left:0;right:0;bottom:0;height:45px;background:var(--band);display:flex;align-items:center}
.p-back .cover-band{padding-left:42px;gap:16px}
.cover-band .brand-name{font-size:6px;color:#fff}
.contact{display:flex;flex-direction:column;gap:3px}
.contact-line{display:flex;align-items:center;gap:4px;color:#ddd}
.contact-line svg{width:5px;height:5px}
.phone{font-size:6px;letter-spacing:.18em}
.email{font-size:4px;font-family:"Open Sans",sans-serif}
.p-front .photo{left:0;top:0;width:231px;height:274px;background:linear-gradient(120deg,#1e1e1e 0%,#5a5a5a 35%,#c8c8c8 60%,#8a8a8a 80%,#d7d7d7)}
.p-front .cover-band{padding:0 18px 0 20px;justify-content:space-between}
.p-front .brand-name{font-size:7px}
.style-guide{font-size:7px;letter-spacing:.45em;color:#bdbdbd;font-weight:400}

/* ---------- row 2 ---------- */
.p-info{left:33px;top:387px}
.p-info .photo.main{left:21px;top:0;width:188px;height:120px;background:linear-gradient(160deg,#5d6e86 0%,#33425a 45%,#8b96a6 100%)}
.p-info .photo.inset{left:126px;top:80px;width:63px;height:63px;border:2px solid #fff;background:linear-gradient(135deg,#c5c5c5,#6e5a48 60%,#3a3a3a)}
.info-title{position:absolute;left:0;right:0;top:157px;text-align:center;font-size:11px;font-weight:300;color:var(--navy);line-height:1.15;text-transform:uppercase;letter-spacing:.02em}
.info-text{position:absolute;left:21px;right:22px;top:191px;columns:2;column-gap:7px;font-family:"Open Sans",sans-serif;font-size:3.5px;line-height:1.45;color:#555;text-align:justify}
.info-text p{margin-bottom:5px}
.p-sig3{left:264px;top:387px;background:#fbfbfb}
.p-com{left:495px;top:387px}
.p-sig3 .sheet-head,.p-com .sheet-head{margin-top:17px}
.p-com .sheet-title{font-size:4.2px}
.sec-gap{margin-top:7px}

/* ---------- row 3 ---------- */
.stage{position:absolute;overflow:hidden}
.stage-label{position:absolute;left:13px;top:13px;font-size:5.5px;letter-spacing:.14em;color:#555}
.box-1{left:33px;top:741px;width:276px;height:213px;background:linear-gradient(160deg,#c4c4c4,#adadad)}
.box-2{left:33px;top:954px;width:276px;height:212px;background:linear-gradient(160deg,#d2d2d2,#bcbcbc)}
.box-lid{position:absolute;left:38px;top:48px;width:200px;height:124px;border-radius:2px;padding:14px 14px 0 0}
.box-1 .box-lid{background:linear-gradient(150deg,#45474c,#2f3034);box-shadow:0 6px 14px rgba(0,0,0,.3)}
.box-2 .box-lid{background:linear-gradient(150deg,#fff,#eeeeee);box-shadow:0 6px 14px rgba(0,0,0,.18)}
.lid-brand{position:absolute;right:14px;top:16px;text-align:right}
.lid-brand .brand-name{font-size:10px}
.box-1 .lid-brand .brand-name{color:#fff}
.box-2 .lid-brand .brand-name{color:var(--navy)}
.lid-brand .brand-mark{width:7px;height:7px}
.lid-sub{font-size:6px;font-weight:600;letter-spacing:.1em;text-transform:uppercase;margin-top:5px}
.box-1 .lid-sub{color:#fff}
.box-2 .lid-sub{color:var(--navy)}
.lid-dots{position:absolute;left:64px;top:56px;width:72px;height:58px}

.cover-2-label{position:absolute;left:334px;top:727px;font-size:5.5px;letter-spacing:.14em;color:#555}
.cover-2{left:334px;top:741px;width:392px;height:270px}
.cover-2 svg.art{position:absolute;left:0;top:0}
.c2-word{position:absolute;left:0;width:196px;top:121px;text-align:center}
.c2-word .brand-name{font-size:12px;color:#5b7090;font-weight:500;letter-spacing:.14em}
.c2-foot{position:absolute;left:60px;top:242px;display:flex;align-items:center;gap:14px}
.c2-foot .brand-name{font-size:6px;color:var(--navy)}
.c2-foot .contact-line{color:var(--navy)}
.c2-title{position:absolute;right:14px;top:208px;text-align:right}
.c2-title h2{font-size:9px;font-weight:300;color:var(--navy);line-height:1.1;text-transform:uppercase}
.c2-title p{font-size:6px;letter-spacing:.35em;color:var(--blue);margin-top:3px;margin-right:-2px}

.stickers{left:450px;top:1040px;width:276px;height:126px;background:#aaa}
.sticker{position:absolute;top:16px;width:92px;height:92px;border-radius:50%;overflow:hidden;background:#f4f4f4;box-shadow:0 2px 6px rgba(0,0,0,.2)}
.sticker.one{left:31px}
.sticker.two{left:155px}
.sticker-top{height:47px;background:var(--sticker-navy);display:flex;flex-direction:column;align-items:center;justify-content:flex-end;padding-bottom:5px;gap:5px}
.sticker-top .brand-name{font-size:5.5px;color:#fff}
.sticker-phone{font-size:7px;color:#fff;letter-spacing:.16em}
.sticker-code{text-align:center;font-size:4px;color:#222;margin-top:6px;font-family:"Open Sans",sans-serif}
</style>
</head>
<body>

<!-- ================= ROW 1 : outside spread ================= -->
<section class="page p-sig2">
  <header class="sheet-head"><span class="brand"><span class="brand-name">Varnex Board</span></span><span class="sheet-title">Signage Grade 2 mm</span></header>
  <div class="sheet-body">
    <div class="swatches">
      <div class="pair"><div class="chips"><span class="chip mw">Matte White</span><span class="chip u">Undercoat</span></div><p class="code">VB-20EU</p></div>
      <div class="pair"><div class="chips"><span class="chip mw">Matte White</span><span class="chip mw">Matte White Print</span></div><p class="code">VB-20E</p></div>
      <div class="pair"><div class="chips"><span class="chip w">High Gloss White</span><span class="chip mw">Matte White</span></div><p class="code">VB-20</p></div>
      <div class="pair"><div class="chips"><span class="chip mw">Matte White Print</span><span class="chip mw">Matte White Print</span></div><p class="code">VB-01</p></div>
      <div class="pair"><div class="chips"><span class="chip mw">Matte White</span><span class="chip k dk">Matte Black</span></div><p class="code">VB-01A</p></div>
      <div class="pair"><div class="chips"><span class="chip k dk">Matte White</span><span class="chip k dk">Matte White</span></div><p class="code">VB-01B</p></div>
      <div class="pair"><div class="chips"><span class="chip mw">Matte White Print</span><span class="chip u">Undercoat Matte White</span></div><p class="code">VB-02</p></div>
      <div class="pair"><div class="chips"><span class="chip w">Gloss White</span><span class="chip mw">Matte White Print</span></div><p class="code">VB-03E</p></div>
    </div>
  </div>
  <header class="sheet-head second"><span class="brand"><span class="brand-name">Varnex Board</span></span><span class="sheet-title">Signage Grade 2 mm</span></header>
  <div class="sheet-body">
    <div class="swatches">
      <div class="pair"><div class="chips"><span class="chip k dk">High Gloss Black</span><span class="chip k dk">High Gloss Black</span></div><p class="code">VB-03GB</p></div>
      <div class="pair"><div class="chips"><span class="chip k dk">High Gloss Black</span><span class="chip k dk">Matte Black</span></div><p class="code">VB-03MB</p></div>
      <div class="pair"><div class="chips"><span class="chip k dk">Matte Black</span><span class="chip k dk">Matte Black</span></div><p class="code">VB-60MB</p></div>
      <div class="pair"><div class="chips"><span class="chip w">Semi-Gloss White Print</span><span class="chip u">Undercoat</span></div><p class="code">VB-03SW</p></div>
      <div class="pair"><div class="chips"><span class="chip w">Semi-Gloss White Print</span><span class="chip w">Semi-Gloss White Print</span></div><p class="code">VB-03SG</p></div>
      <div class="pair"><div class="chips"><span class="chip mw">Matte White</span><span class="chip k dk">Matte Black</span></div><p class="code">VB-03MW</p></div>
      <div class="pair"><div class="chips"><span class="chip w">Matte White</span><span class="chip u">Undercoat</span></div><p class="code">VB-03U</p></div>
      <div class="pair"><div class="chips"><span class="chip u">Undercoat</span><span class="chip u">Undercoat</span></div><p class="code">VB-03UU</p></div>
      <div class="pair"><div class="chips"><span class="chip w">High Gloss White</span><span class="chip w">High Gloss White</span></div><p class="code">VB-03WW</p></div>
    </div>
  </div>
</section>

<section class="page p-back">
  <div class="cover-word"><span class="brand"><span class="brand-name">Varnex Board</span></span></div>
  <footer class="cover-band">
    <span class="brand"><i class="brand-mark"></i><span class="brand-name">Varnex Board</span></span>
    <div class="contact">
      <span class="contact-line"><svg viewBox="0 0 10 10" aria-hidden="true"><circle cx="5" cy="5" r="4.4" fill="none" stroke="#ddd" stroke-width=".9"/><path d="M3.4 2.8c.4-.3.8 0 1 .5l.2.6c.1.3-.1.5-.3.7.3.7.7 1.1 1.3 1.4.2-.2.4-.4.7-.3l.6.2c.5.2.7.6.4 1-.6.7-1.6.5-2.6-.4S2.7 3.4 3.4 2.8z" fill="#ddd"/></svg><span class="phone">1300 584 906</span></span>
      <span class="contact-line"><svg viewBox="0 0 10 10" aria-hidden="true"><circle cx="5" cy="5" r="4.4" fill="none" stroke="#ddd" stroke-width=".9"/><rect x="2.8" y="3.5" width="4.4" height="3" fill="none" stroke="#ddd" stroke-width=".7"/><path d="M2.8 3.5 5 5.2 7.2 3.5" fill="none" stroke="#ddd" stroke-width=".7"/></svg><span class="email">mail@varnexboard.com</span></span>
    </div>
  </footer>
</section>

<section class="page p-front">
  <div class="photo" role="img" aria-label="Black and white photograph of a curved building facade clad in composite panels with a wall-mounted sign"></div>
  <footer class="cover-band">
    <span class="brand"><i class="brand-mark"></i><span class="brand-name">Varnex Board</span></span>
    <span class="style-guide">STYLE GUIDE</span>
  </footer>
</section>

<!-- ================= ROW 2 : inside spread ================= -->
<section class="page p-info">
  <div class="photo main" role="img" aria-label="Dusk photograph of a car showroom with dark composite panel cladding and a tall signage pylon"></div>
  <div class="photo inset" role="img" aria-label="Close-up photograph of a shopfront entrance with a dimensional sign on a panel wall"></div>
  <h1 class="info-title">Light Commercial<br>Composite</h1>
  <div class="info-text">
    <p>Our aluminium composite panel is built for lasting quality in 4mm sheets that are easy to cut, route and fold. Each panel pairs two aluminium skins with a solid core, making it a trusted choice for façade cladding and wall lining. A durable coated finish keeps its gloss and colour with little upkeep. Panels come in a broad range of colours and textures to suit current market trends, and we take care to meet each client's sizes at a fair price.</p>
    <p>Our aluminium composite panel is built for lasting quality in 4mm sheets that are easy to cut, route and fold. Each panel pairs two aluminium skins with a solid core, making it a trusted choice for façade cladding and wall lining. A durable coated finish keeps its gloss and colour with little upkeep. Panels come in a broad range of colours and textures to suit current market trends, and we take care to meet each client's needs and sizes.</p>
    <p>Our aluminium composite panel is built for lasting quality in 4mm sheets that are easy to cut, route and fold. Each panel pairs two aluminium skins with a solid core, making it a trusted choice for façade cladding and wall lining. A durable coated finish keeps its gloss and colour with little upkeep. Panels come in a broad range of colours and textures to suit current trends, and we take care to meet each client's sizes at a fair price.</p>
    <p>Our aluminium composite panel is built for lasting quality in 4mm sheets that are easy to cut, route and fold. Each panel pairs two aluminium skins with a solid core, making it a trusted choice for façade cladding and wall lining. A durable coated finish keeps its gloss and colour with little upkeep. Panels come in a broad range of colours and textures to suit trends and needs.</p>
  </div>
</section>

<section class="page p-sig3">
  <header class="sheet-head"><span class="brand"><span class="brand-name">Varnex Board</span></span><span class="sheet-title">Signage Grade 3 mm</span></header>
  <div class="sheet-body">
    <div class="swatches tight">
      <div class="pair"><div class="chips"><span class="chip w">High Gloss White</span><span class="chip k dk">High Gloss Black</span></div><p class="code">VB-31W</p></div>
      <div class="pair"><div class="chips"><span class="chip k dk">High Gloss Black</span><span class="chip w">High Gloss White</span></div><p class="code">VB-31B</p></div>
      <div class="pair"><div class="chips"><span class="chip bs">Brush Silver</span><span class="chip ra">Raw Aluminium</span></div><p class="code">VB-32A</p></div>
      <div class="pair"><div class="chips"><span class="chip r dk">High Gloss Red</span><span class="chip w">High Gloss White</span></div><p class="code">VB-34W</p></div>
      <div class="pair"><div class="chips"><span class="chip y">High Gloss Yellow</span><span class="chip w">High Gloss White</span></div><p class="code">VB-35W</p></div>
      <div class="pair"><div class="chips"><span class="chip pb dk">High Gloss Process Blue</span><span class="chip w">High Gloss White</span></div><p class="code">VB-36W</p></div>
      <div class="pair"><div class="chips"><span class="chip rb dk">High Gloss Reflex Blue</span><span class="chip w">High Gloss White</span></div><p class="code">VB-37W</p></div>
      <div class="pair"><div class="chips"><span class="chip fg dk">High Gloss Forest Green</span><span class="chip w">High Gloss White</span></div><p class="code">VB-38W</p></div>
      <div class="pair"><div class="chips"><span class="chip hr dk">High Gloss Heritage Red</span><span class="chip w">High Gloss White</span></div><p class="code">VB-39W</p></div>
      <div class="pair"><div class="chips"><span class="chip o dk">High Gloss Orange</span><span class="chip w">High Gloss White</span></div><p class="code">VB-40W</p></div>
      <div class="pair"><div class="chips"><span class="chip nb dk">High Gloss Navy Blue</span><span class="chip w">High Gloss White</span></div><p class="code">VB-42W</p></div>
      <div class="pair"><div class="chips"><span class="chip ch">Metallic Charcoal</span><span class="chip w">High Gloss White</span></div><p class="code">VB-44W</p></div>
      <div class="pair"><div class="chips"><span class="chip eg dk">High Gloss Emerald Green</span><span class="chip w">High Gloss White</span></div><p class="code">VB-49W</p></div>
      <div class="pair"><div class="chips"><span class="chip ms">Metallic Silver</span><span class="chip w">High Gloss White</span></div><p class="code">VB-52</p></div>
      <div class="pair"><div class="chips"><span class="chip sg dk">High Gloss Steel Grey</span><span class="chip w">High Gloss White</span></div><p class="code">VB-61W</p></div>

      <h3 class="sec wide sec-gap">Signage Grade 4 mm</h3>
      <h3 class="sec sec-gap">Light Commercial<br>Grade Oversized</h3>
      <div class="pair"><div class="chips"><span class="chip mw">Matte White</span><span class="chip k dk">Matte Black</span></div><p class="code">VB-65</p></div>
      <div class="pair"><div class="chips"><span class="chip u">Undercoat</span><span class="chip u">Undercoat</span></div><p class="code">VB-21UU</p></div>
      <div class="pair"><div class="chips"><span class="chip w">High Gloss White</span><span class="chip mw">Matte White</span></div><p class="code">VB-200</p></div>

      <h3 class="sec full sec-gap">Light Commercial Grade 3mm</h3>
      <div class="pair"><div class="chips"><span class="chip w">High Gloss White</span><span class="chip mw">Matte White</span></div><p class="code">VL-03</p></div>
      <div class="pair"><div class="chips"><span class="chip w">High Gloss White</span><span class="chip k dk">High Gloss Black</span></div><p class="code">VL-03WB</p></div>
      <div class="pair"><div class="chips"><span class="chip k dk">High Gloss Black</span><span class="chip k dk">Matte Black</span></div><p class="code">VL-33</p></div>
    </div>
  </div>
</section>

<section class="page p-com">
  <header class="sheet-head"><span class="brand"><span class="brand-name">Varnex Board</span></span><span class="sheet-title">Light Commercial Grade Specialty Surfaces</span></header>
  <div class="sheet-body">
    <div class="swatches tight">
      <div class="pair"><div class="chips"><span class="chip gold">Mirror Gold</span><span class="chip u">Undercoat</span></div><p class="code">VA-30</p></div>
      <div class="pair"><div class="chips"><span class="chip mir">Mirror Silver</span><span class="chip u">Undercoat</span></div><p class="code">VA-31</p></div>
      <div class="pair"><div class="chips"><span class="chip bs">Brush Silver</span><span class="chip ra">Raw Aluminium</span></div><p class="code">VA-32</p></div>
      <div class="pair"><div class="chips"><span class="chip cu dk">Brush Copper</span><span class="chip bg">Brush Gold</span></div><p class="code">VA-60</p></div>
      <div class="pair"><div class="chips"><span class="chip emb">Milled Embossed</span><span class="chip ra">Raw Aluminium</span></div><p class="code">VA-80</p></div>
      <div class="pair"><div class="chips"><span class="chip emb">Diamond Embossed</span><span class="chip ra">Raw Aluminium</span></div><p class="code">VA-81</p></div>
      <div class="pair"><div class="chips"><span class="chip rust dk">Textured Rust</span><span class="chip u">Undercoat</span></div><p class="code">VA-91</p></div>
      <div class="pair"><div class="chips"><span class="chip ant">Mirror Anthracite Silver</span><span class="chip u">Undercoat</span></div><p class="code">VA-105</p></div>
      <div class="pair"><div class="chips"><span class="chip ss">Brush Stainless Steel</span><span class="chip mw">Stainless Steel</span></div><p class="code">VA-300</p></div>

      <h3 class="sec full sec-gap">Commercial Grade</h3>
      <div class="pair"><div class="chips"><span class="chip wd1 dk">Golden Wattle</span><span class="chip w">High Gloss White</span></div><p class="code">VP-93</p></div>
      <div class="pair"><div class="chips"><span class="chip wd2 dk">Walnut</span><span class="chip w">High Gloss White</span></div><p class="code">VP-94</p></div>
      <div class="pair"><div class="chips"><span class="chip wd3 dk">Vintage Allspice</span><span class="chip w">High Gloss White</span></div><p class="code">VP-95</p></div>
      <div class="pair"><div class="chips"><span class="chip wd4 dk">Wenge Dark</span><span class="chip w">High Gloss White</span></div><p class="code">VP-96</p></div>
      <div class="pair"><div class="chips"><span class="chip wd5 dk">Sorrento Oak</span><span class="chip w">High Gloss White</span></div><p class="code">VP-97</p></div>
      <div class="pair"><div class="chips"><span class="chip wd6 dk">Spotted Gum</span><span class="chip w">High Gloss White</span></div><p class="code">VP-98</p></div>

      <h3 class="sec full sec-gap">Commercial Grade 4 mm</h3>
      <div class="pair"><div class="chips"><span class="chip pm">PVDF Metallic Silver</span><span class="chip w">High Gloss White</span></div><p class="code">VP-119</p></div>
      <div class="pair"><div class="chips"><span class="chip w">High Gloss White</span><span class="chip mw">PVDF Matte White</span></div><p class="code">VP-120</p></div>
      <div class="pair"><div class="chips"><span class="chip pk dk">High Gloss Black</span><span class="chip pk dk">PVDF Matte Black</span></div><p class="code">VP-133</p></div>
      <div class="pair"><div class="chips"><span class="chip pk dk">PVDF Metallic Black</span><span class="chip u">Undercoat</span></div><p class="code">VP-107</p></div>
      <div class="pair"><div class="chips"><span class="chip pk dk">Feve Semi Gloss Black</span><span class="chip mw">Feve Semi Gloss White</span></div><p class="code">VP-233</p></div>
    </div>
  </div>
</section>

<!-- ================= ROW 3 : box, alternate cover, label ================= -->
<section class="stage box-1">
  <p class="stage-label">Carton Box Option 1</p>
  <div class="box-lid">
    <div class="lid-brand"><span class="brand"><i class="brand-mark"></i><span class="brand-name">Varnex Board</span></span><p class="lid-sub">Sample Colours</p></div>
    <svg class="lid-dots" viewBox="0 0 72 58" aria-hidden="true">
      <circle cx="20" cy="26" r="8" fill="#0b9a48"/><circle cx="36" cy="16" r="7" fill="#e6e6e6"/><circle cx="52" cy="22" r="8" fill="#0b86c9"/>
      <circle cx="37" cy="32" r="9" fill="#e3191f"/><circle cx="20" cy="42" r="7" fill="#bfc2c6"/><circle cx="55" cy="40" r="9" fill="#e6d59a"/><circle cx="38" cy="50" r="8" fill="#a8643a"/>
    </svg>
  </div>
</section>

<section class="stage box-2">
  <p class="stage-label">Carton Box Option 2</p>
  <div class="box-lid">
    <div class="lid-brand"><span class="brand"><i class="brand-mark"></i><span class="brand-name">Varnex Board</span></span><p class="lid-sub">Sample Colours</p></div>
    <svg class="lid-dots" viewBox="0 0 72 58" aria-hidden="true">
      <circle cx="20" cy="26" r="8" fill="#0b9a48"/><circle cx="36" cy="16" r="7" fill="#d9d9d9"/><circle cx="52" cy="22" r="8" fill="#0b86c9"/>
      <circle cx="37" cy="32" r="9" fill="#e3191f"/><circle cx="20" cy="42" r="7" fill="#bfc2c6"/><circle cx="55" cy="40" r="9" fill="#e6d59a"/><circle cx="38" cy="50" r="8" fill="#a8643a"/>
    </svg>
  </div>
</section>

<p class="cover-2-label">Cover Option 2</p>
<section class="stage cover-2">
  <svg class="art" width="392" height="270" viewBox="0 0 392 270">
    <rect x="0" y="0" width="196" height="270" fill="#2e4566"/>
    <polygon points="0,254 196,187 196,270 0,270" fill="#fff"/>
    <defs>
      <linearGradient id="signPhoto" x1="0" y1="0" x2="1" y2="1"><stop offset="0" stop-color="#f6f2e8"/><stop offset="1" stop-color="#d9d2c2"/></linearGradient>
      <linearGradient id="buildPhoto" x1="0" y1="0" x2="1" y2="1"><stop offset="0" stop-color="#8996aa"/><stop offset=".5" stop-color="#34435c"/><stop offset="1" stop-color="#5a6a84"/></linearGradient>
    </defs>
    <g role="img" aria-label="Photograph of a dimensional brand sign mounted on a warm cream wall">
      <polygon points="196,0 392,0 392,118 196,196" fill="url(#signPhoto)"/>
    </g>
    <g role="img" aria-label="Photograph of a showroom facade with dark composite panel cladding">
      <polygon points="196,196 392,118 392,180 225,270 196,270" fill="url(#buildPhoto)"/>
    </g>
    <polygon points="225,270 392,180 392,270" fill="#fff"/>
  </svg>
  <div class="c2-word"><span class="brand"><span class="brand-name">Varnex Board</span></span></div>
  <div class="c2-foot">
    <span class="brand"><i class="brand-mark"></i><span class="brand-name">Varnex Board</span></span>
    <div class="contact">
      <span class="contact-line"><svg viewBox="0 0 10 10" aria-hidden="true"><circle cx="5" cy="5" r="4.4" fill="none" stroke="#2f8fd6" stroke-width=".9"/><path d="M3.4 2.8c.4-.3.8 0 1 .5l.2.6c.1.3-.1.5-.3.7.3.7.7 1.1 1.3 1.4.2-.2.4-.4.7-.3l.6.2c.5.2.7.6.4 1-.6.7-1.6.5-2.6-.4S2.7 3.4 3.4 2.8z" fill="#2f8fd6"/></svg><span class="phone">1300 584 906</span></span>
      <span class="contact-line"><svg viewBox="0 0 10 10" aria-hidden="true"><circle cx="5" cy="5" r="4.4" fill="none" stroke="#2f8fd6" stroke-width=".9"/><rect x="2.8" y="3.5" width="4.4" height="3" fill="none" stroke="#2f8fd6" stroke-width=".7"/><path d="M2.8 3.5 5 5.2 7.2 3.5" fill="none" stroke="#2f8fd6" stroke-width=".7"/></svg><span class="email">mail@varnexboard.com</span></span>
    </div>
  </div>
  <div class="c2-title">
    <h2>Light<br>Commercial<br>Composite</h2>
    <p>STYLE GUIDE</p>
  </div>
</section>

<section class="stage stickers">
  <div class="sticker one">
    <div class="sticker-top"><span class="brand"><span class="brand-name">Varnex Board</span></span><span class="sticker-phone">1300 584 906</span></div>
    <p class="sticker-code">Product Code</p>
  </div>
  <div class="sticker two">
    <div class="sticker-top"><span class="brand"><span class="brand-name">Varnex Board</span></span><span class="sticker-phone">1300 584 906</span></div>
    <p class="sticker-code">Product Code</p>
  </div>
</section>

</body>
</html>
```